Carpet cleaning company focused on high quality needs business cards

We are a growing company that just merged with another company and need to design a new business card. We do both residential as well as commercial cleaning. We do carpet, tile & grout, upholstery, hard floors, and stain & pet odor removal. We treat our customers like family and strive to achieve outstanding results with every job.

```html
<!DOCTYPE html>
<html lang="en">
<head>
<meta charset="utf-8">
<title>Hearthstone Steam Cleaning – Business Card</title>
<link href="https://fonts.googleapis.com/css2?family=Open+Sans:wght@400;600;700;800&display=swap" rel="stylesheet">
<style>
  :root {
    --stage: #232323;
    --brand-red: #ee4a43;
    --brand-blue: #0a82c4;
    --ink: #111111;
    --paper: #ffffff;
    --rule: #1a1a1a;
  }
  * { box-sizing: border-box; margin: 0; padding: 0; }
  html, body { width: 1200px; height: 780px; overflow: hidden; }
  body {
    background: var(--stage);
    font-family: "Open Sans", Arial, sans-serif;
    position: relative;
  }
  .card {
    position: absolute;
    width: 560px;
    height: 320px;
    border-radius: 22px;
    overflow: hidden;
  }

  /* Front: services side */
  .card-front {
    left: 50px; top: 60px;
    background: var(--brand-red);
    color: var(--paper);
  }
  .front-brand {
    position: absolute;
    left: 0; right: 0; top: 78px;
    display: flex; align-items: center; justify-content: center; gap: 16px;
  }
  .brand-mark {
    width: 58px; height: 58px;
    background: var(--paper);
    flex: none;
  }
  .brand-name {
    font-weight: 800;
    color: var(--ink);
    line-height: 1.02;
    text-transform: uppercase;
  }
  .front-brand .brand-name { font-size: 30px; }
  .services-heading {
    position: absolute;
    left: 40px; right: 40px; top: 196px;
    display: flex; align-items: center; gap: 12px;
    font-size: 13px; font-weight: 700; letter-spacing: 0.5px;
    text-transform: uppercase;
  }
  .services-heading::before,
  .services-heading::after {
    content: ""; flex: 1; height: 1px; background: var(--paper);
  }
  .services-list {
    position: absolute;
    left: 20px; right: 20px; top: 224px;
    text-align: center;
    font-size: 14px; line-height: 1.6;
  }
  .services-list .dot { margin: 0 4px; }

  /* Back: contact side */
  .card-back {
    left: 590px; top: 400px;
    background: var(--paper);
    color: var(--ink);
  }
  .back-brand {
    position: absolute; left: 34px; top: 30px;
    display: flex; align-items: center; gap: 12px;
  }
  .back-brand .brand-mark { background: var(--brand-red); width: 44px; height: 44px; }
  .back-brand .brand-name { font-size: 20px; }
  .holder {
    position: absolute; left: 0; top: 110px;
    padding-left: 34px;
    border-left: 12px solid var(--brand-red);
  }
  .holder-name { font-size: 30px; font-weight: 700; line-height: 1.1; }
  .holder-name .first { color: var(--brand-red); }
  .holder-name .last { color: var(--brand-blue); }
  .holder-title { font-size: 16px; font-weight: 600; margin-top: 2px; }
  .name-rule {
    position: absolute; left: 280px; right: 30px; top: 150px;
    height: 2px; background: var(--rule);
  }
  .contact-list {
    position: absolute; left: 46px; top: 196px;
    list-style: none; font-size: 15px; line-height: 1.55;
  }
  .contact-list li { display: flex; align-items: center; gap: 10px; }
  .contact-list svg { width: 14px; height: 14px; flex: none; }
  .address {
    position: absolute; right: 34px; top: 172px;
    text-align: right; font-size: 15px; line-height: 1.5;
  }
  .footer-bands {
    position: absolute; left: 0; bottom: 0; width: 560px; height: 56px;
  }
</style>
</head>
<body>

  <section class="card card-front" aria-label="Business card front">
    <div class="front-brand">
      <span class="brand-mark"></span>
      <span class="brand-name">Hearthstone<br>Steam Cleaning</span>
    </div>
    <h2 class="services-heading">Our Services</h2>
    <p class="services-list">
      <span class="dot">●</span>Both residential as well as commercial cleaning<br>
      <span class="dot">●</span>Carpet <span class="dot">●</span>Tile &amp; grout <span class="dot">●</span>Upholstery <span class="dot">●</span>Hard floors <span class="dot">●</span>Stain &amp; pet odor removal
    </p>
  </section>

  <section class="card card-back" aria-label="Business card back">
    <div class="back-brand">
      <span class="brand-mark"></span>
      <span class="brand-name">Hearthstone<br>Steam Cleaning</span>
    </div>

    <div class="holder">
      <p class="holder-name"><span class="first">Marta</span> <span class="last">Kovalenko</span></p>
      <p class="holder-title">Managing Director</p>
    </div>
    <div class="name-rule"></div>

    <ul class="contact-list">
      <li>
        <svg viewBox="0 0 24 24" aria-hidden="true"><path fill="#ee4a43" d="M6.6 10.8a15 15 0 0 0 6.6 6.6l2.2-2.2a1 1 0 0 1 1-.25 11.4 11.4 0 0 0 3.6.57 1 1 0 0 1 1 1V20a1 1 0 0 1-1 1A17 17 0 0 1 3 4a1 1 0 0 1 1-1h3.5a1 1 0 0 1 1 1 11.4 11.4 0 0 0 .57 3.6 1 1 0 0 1-.25 1z"/></svg>
        (555) 014-2387
      </li>
      <li>
        <svg viewBox="0 0 24 24" aria-hidden="true"><rect x="2" y="5" width="20" height="14" rx="2" fill="#ee4a43"/><path d="M3 6l9 7 9-7" fill="none" stroke="#fff" stroke-width="2"/></svg>
        hello@hearthstoneclean.com
      </li>
      <li>
        <svg viewBox="0 0 24 24" aria-hidden="true"><circle cx="12" cy="12" r="10" fill="#ee4a43"/><path d="M2 12h20M12 2c3 3 3 17 0 20M12 2c-3 3-3 17 0 20" fill="none" stroke="#fff" stroke-width="1.5"/></svg>
        www.hearthstoneclean.com
      </li>
    </ul>

    <p class="address">418 Linden Ave. Suite<br>120 Maple Grove, TX 75001</p>

    <svg class="footer-bands" viewBox="0 0 560 56" aria-hidden="true">
      <polygon points="0,30 400,30 440,8 560,8 560,56 0,56" fill="#ee4a43"/>
      <polygon points="0,36 410,36 440,20 560,20 560,56 0,56" fill="#ffffff"/>
      <polygon points="0,40 414,40 444,24 560,24 560,56 0,56" fill="#0a82c4"/>
    </svg>
  </section>

</body>
</html>
```